Dental Practice Website design

Design a new website for Brambleford Dental Practice.
Design should be warm, neutral in colour, with some small amount of bright colour if needed but kept to a minimum. Website should look professional, high end. Home page should be easy to navigate and simple for patients to be able to book online.
Logo in files along with some examples of websites that we like. Please ask if any further info needed.
Menu should have:
About
New Patients
Treatments
Fees
Contact Us

Industry/Entity Type

Dentistry

Number of Pages Required

4 page

Font styles to use
Sans Serif

Colors

Designer to choose colors to be used in the design.

Requirements
Must have
• Ravelle ratings badge, book online button,
Nice to have
• neutral, relaxing colours
Should not have
• harsh, bright colours!

```html
<!DOCTYPE html>
<html lang="en">
<head>
<meta charset="utf-8">
<title>Brambleford Dental Practice</title>
<link rel="stylesheet" href="https://fonts.googleapis.com/css2?family=Heebo:wght@300;400;500;700;800&display=swap">
<style>
:root{
  --sand:#a89a8b;
  --sand-light:#c9bfb3;
  --accent:#a08f7c;
  --ink:#1d2b2e;
  --ink-soft:#25363a;
  --paper:#f4f2ef;
  --text:#5f5f5f;
  --white:#ffffff;
}
*{margin:0;padding:0;box-sizing:border-box}
html,body{width:1200px;height:3574px;overflow:hidden}
body{font-family:"Heebo",Arial,sans-serif;background:var(--paper);color:var(--text);position:relative}
.abs{position:absolute}
.ph{position:absolute}

/* hero */
.hero{position:absolute;left:0;top:0;width:1200px;height:570px;background:linear-gradient(90deg,#a3958a 0%,#a99b8e 55%,#ae9f91 100%);overflow:hidden}
.hero-photo{left:560px;top:0;width:640px;height:570px;background:linear-gradient(90deg,rgba(169,155,142,0) 0%,rgba(160,132,110,.35) 30%,rgba(150,118,92,.55) 60%,rgba(170,145,125,.45) 100%)}
.nav{left:325px;top:0;width:795px;height:58px}
.nav ul{position:absolute;left:0;top:0;width:100%;height:58px;display:flex;justify-content:center;list-style:none;padding-left:30px}
.nav li{color:var(--white);font-size:15px;line-height:58px;margin:0 24px}
.nav li.active{font-weight:700}
.logo{color:var(--white);font-weight:300;text-align:center;line-height:1}
.logo .name{font-size:30px;letter-spacing:1px}
.logo .sub{font-size:15px;letter-spacing:1.5px;margin-top:4px}
.hero-logo{left:114px;top:66px;width:160px}
.eyebrow{left:114px;top:170px;color:var(--white);font-size:22px;font-weight:700;letter-spacing:.3px}
.hero h1{position:absolute;left:114px;top:202px;width:460px;color:var(--white);font-size:42px;font-weight:800;line-height:56px;letter-spacing:.5px}
.hero-lede{left:114px;top:372px;width:440px;color:var(--white);font-size:15px;line-height:28px}
.btn{position:absolute;display:flex;align-items:center;justify-content:center;font-size:15px;font-weight:500;height:43px}
.btn-light{left:114px;top:447px;width:192px;background:var(--white);color:var(--ink)}
.btn-ghost{left:329px;top:447px;width:167px;border:1.5px solid var(--white);color:var(--white)}

/* headings */
.sec-title{position:absolute;left:0;width:1200px;text-align:center;color:var(--ink);font-weight:700;text-transform:uppercase}
.rule{position:absolute;height:3px;background:var(--accent);border-radius:2px}

/* welcome */
.welcome-title{top:640px;font-size:29px;line-height:44px}
.welcome-photo{left:112px;top:785px;width:488px;height:400px;border-radius:24px;background:linear-gradient(135deg,#b9c6cf 0%,#e8e2dc 45%,#a9bccb 100%)}
.welcome-copy{left:655px;top:808px;width:435px;font-size:14px;line-height:28.5px;text-align:justify}
.welcome-copy .lead{color:var(--accent);font-weight:500}
.welcome-copy p{margin-bottom:13px}
.btn-dark{left:655px;top:1112px;width:134px;background:var(--ink);color:var(--white)}

/* services */
.services-bg{left:0;top:1200px;width:1200px;height:671px;background:linear-gradient(180deg,#f4f2ef 0%,#ebe7e2 50%,#efece8 100%)}
.services-title{top:1258px;font-size:29px}
.services-lede{left:215px;top:1322px;width:770px;text-align:center;font-size:15px;line-height:31px}
.card{position:absolute;top:1410px;width:232px;height:360px;background:var(--white);border-radius:18px 18px 116px 116px / 18px 18px 90px 90px;text-align:center}
.card .pic{position:absolute;left:29px;top:28px;width:174px;height:174px;border-radius:50%}
.card.active .pic{border:7px solid var(--ink)}
.card h3{position:absolute;left:0;top:222px;width:100%;color:var(--ink);font-size:15px;font-weight:500;letter-spacing:.3px}
.card p{position:absolute;left:22px;top:250px;width:188px;font-size:12px;line-height:23px}
.card svg{position:absolute;left:109px;top:330px}

/* team */
.team{position:absolute;left:0;top:1871px;width:1200px;height:538px;background:linear-gradient(135deg,var(--ink) 0%,var(--ink-soft) 60%,#1a272a 100%)}
.team h2{position:absolute;left:112px;top:100px;color:var(--white);font-size:28px;font-weight:700}
.team .rule{left:112px;top:154px;width:194px;background:var(--white)}
.team-copy{position:absolute;left:112px;top:174px;width:450px;color:var(--white);font-size:15.5px;line-height:31px;text-align:justify}
.btn-sand{left:112px;top:384px;width:122px;background:var(--sand);color:var(--white)}
.team-photo{border-radius:16px}

/* practice */
.practice-title{top:2465px;font-size:28px}
.practice-copy{left:200px;top:2540px;width:800px;text-align:center;font-size:15px;line-height:31px}
.practice-copy p{margin-bottom:13px}
.field{position:absolute;top:2765px;height:49px;background:var(--white);font-size:13.5px;color:#666;padding-left:22px;display:flex;align-items:center}
.field svg{position:absolute;right:22px;top:18px}
.btn-sub{left:795px;top:2765px;width:198px;height:49px;background:var(--ink);color:var(--white);font-weight:700}

/* gallery */
.tile{top:2885px;width:231px;height:312px;border-radius:14px}
.follow{left:428px;top:3014px;width:344px;height:62px;background:rgba(244,242,239,.95);display:flex;align-items:center;justify-content:center;color:var(--ink);font-size:19px;font-weight:500}

/* footer */
.footer{position:absolute;left:0;top:3282px;width:1200px;height:292px;background:linear-gradient(180deg,#e2dbd3 0%,#d6cdc3 100%)}
.footer-logo{left:520px;top:3358px;width:160px}
.footer-logo .name,.footer-logo .sub{color:var(--accent)}
.footer-nav{position:absolute;left:0;top:3440px;width:1200px;display:flex;justify-content:center;list-style:none}
.footer-nav li{color:var(--ink);font-size:15px;margin:0 15px}
.social{position:absolute;top:3490px;width:38px;height:38px;background:var(--white);display:flex;align-items:center;justify-content:center}
.social.on{background:var(--ink)}
.social span{width:8px;height:8px;border-radius:50%;background:var(--ink)}
.social.on span{background:var(--white)}
.copy{position:absolute;left:0;top:3544px;width:1200px;text-align:center;font-size:11.5px;color:var(--ink)}
.badge{left:990px;top:3508px;display:flex;align-items:center;gap:6px;color:var(--white);font-size:22px;font-weight:400}
.badge i{display:block;width:12px;height:12px;background:var(--white)}
</style>
</head>
<body>

<section class="hero">
  <div class="ph hero-photo" role="img" aria-label="Portrait of a smiling woman with long wavy hair"></div>
  <svg class="abs" style="left:0;top:530px" width="1200" height="40" viewBox="0 0 1200 40">
    <path d="M0 30 L60 22 L1140 22 L1200 12 L1200 40 L0 40 Z" fill="#f4f2ef"/>
    <path d="M60 22 L1140 22" stroke="#1d2b2e" stroke-width="6"/>
  </svg>
  <nav class="abs nav">
    <svg class="abs" style="left:0;top:0" width="795" height="58" viewBox="0 0 795 58"><path d="M0 0 H795 L765 58 H30 Z" fill="#1d2b2e"/></svg>
    <ul>
      <li class="active">HOME</li><li>About Us</li><li>New Patients</li><li>Treatments</li><li>Fees</li><li>Contact Us</li>
    </ul>
  </nav>
  <div class="abs logo hero-logo"><div class="name">BRAMBLEFORD</div><div class="sub">DENTAL PRACTICE</div></div>
  <div class="abs eyebrow">WHERE SMILES BEGIN</div>
  <h1>YOUR TRUSTED FAMILY DENTIST IN THORNBURY VALE</h1>
  <p class="abs hero-lede">Our team of dedicated dentists, hygienists and support staff are here to provide you with exceptional dental care.</p>
  <div class="btn btn-light">Book an Appointment</div>
  <div class="btn btn-ghost">Contact Us Today</div>
</section>

<h2 class="sec-title welcome-title">Welcome to our friendly dental practice nestled<br>in the heart of beautiful Thornbury Vale, UK.</h2>
<div class="rule" style="left:450px;top:738px;width:300px"></div>
<div class="ph welcome-photo" role="img" aria-label="Dentist examining a smiling patient"></div>
<div class="abs welcome-copy">
  <p class="lead">Our team of dedicated dentists, hygienists and support staff are here to provide you with exceptional dental care.</p>
  <p>With a wide array of services, including general and cosmetic dentistry, orthodontics and emergency care, we're confident that we can deliver the highest quality treatment to you and your loved ones.</p>
  <p>At our practice, we believe that a visit to the dentist should be a comfortable and positive experience. We strive to create a warm and welcoming atmosphere where our patients can feel at ease and confident in the care they receive.</p>
</div>
<div class="btn btn-dark">Explore More</div>

<div class="ph services-bg" role="img" aria-label="Faint background of a dental treatment room"></div>
<h2 class="sec-title services-title">Services We Offer</h2>
<div class="rule" style="left:504px;top:1306px;width:192px"></div>
<p class="abs services-lede">We are passionate about improving dental health and helping you achieve your brightest smile and are honoured that you're considering us for your dental needs.</p>

<div class="card" style="left:112px">
  <div class="ph pic" role="img" aria-label="Smiling patient in the dental chair" style="background:linear-gradient(135deg,#cfdbe3,#9fb6c6)"></div>
  <h3>GENERAL DENTISTRY</h3>
  <p>Ut enim ad minima veniam, quis nostrum exercitationem ullam corporis suscipit labor</p>
  <svg width="14" height="14" viewBox="0 0 14 14"><circle cx="7" cy="7" r="7" fill="#a08f7c"/><path d="M5 4 L9 7 L5 10" stroke="#fff" stroke-width="1.6" fill="none"/></svg>
</div>
<div class="card active" style="left:360px">
  <div class="ph pic" role="img" aria-label="Patient with a tooth shade guide" style="background:linear-gradient(135deg,#e9e6e2,#b9b2aa)"></div>
  <h3>COSMETIC DENTISTRY</h3>
  <p>Ut enim ad minima veniam, quis nostrum exercitationem ullam corporis suscipit labor</p>
  <svg width="14" height="14" viewBox="0 0 14 14"><circle cx="7" cy="7" r="7" fill="#1d2b2e"/><path d="M5 4 L9 7 L5 10" stroke="#fff" stroke-width="1.6" fill="none"/></svg>
</div>
<div class="card" style="left:608px">
  <div class="ph pic" role="img" aria-label="Close-up of teeth with braces" style="background:linear-gradient(135deg,#c7bfe0,#a79686)"></div>
  <h3>ORTHODONTICS</h3>
  <p>Ut enim ad minima veniam, quis nostrum exercitationem ullam corporis suscipit labor</p>
  <svg width="14" height="14" viewBox="0 0 14 14"><circle cx="7" cy="7" r="7" fill="#a08f7c"/><path d="M5 4 L9 7 L5 10" stroke="#fff" stroke-width="1.6" fill="none"/></svg>
</div>
<div class="card" style="left:856px">
  <div class="ph pic" role="img" aria-label="Man holding his cheek with toothache" style="background:linear-gradient(135deg,#6d6a6a,#2f2e30)"></div>
  <h3>EMERGENCY CARE</h3>
  <p>Ut enim ad minima veniam, quis nostrum exercitationem ullam corporis suscipit labor</p>
  <svg width="14" height="14" viewBox="0 0 14 14"><circle cx="7" cy="7" r="7" fill="#a08f7c"/><path d="M5 4 L9 7 L5 10" stroke="#fff" stroke-width="1.6" fill="none"/></svg>
</div>

<section class="team">
  <h2>JOIN OUR TEAM</h2>
  <div class="rule"></div>
  <p class="team-copy">We are delighted to introduce you to our experienced and compassionate dental team. Our team comprises highly skilled dental professionals who are dedicated to providing you with high-quality dental care services. Led by our experienced dentist, each member of our team brings their own unique set of skills and expertise.</p>
  <div class="btn btn-sand">Read More</div>
  <div class="ph team-photo" role="img" aria-label="Dental nurse in blue scrubs with arms folded" style="left:620px;top:87px;width:216px;height:313px;background:linear-gradient(180deg,#e8ecef,#6f95c4)"></div>
  <div class="ph team-photo" role="img" aria-label="Dentist treating a patient in the chair" style="left:872px;top:139px;width:216px;height:313px;background:linear-gradient(160deg,#d9e0e5,#7e99b3 60%,#2f5a86)"></div>
</section>

<h2 class="sec-title practice-title">Join Our Practice</h2>
<div class="rule" style="left:534px;top:2514px;width:132px"></div>
<div class="abs practice-copy">
  <p>If you're looking for an exceptional dental practice, we're here to help! Our team is made up of highly skilled professionals who are dedicated to ensuring that all our patients receive top-notch care in a welcoming and comfortable environment.</p>
  <p>Whether you need a routine examination or a more specialised treatment, we have all the resources to provide you with the best dental care possible. Our practice is always up-to-date with the latest techniques and technologies to make sure that our patients receive the best possible results.</p>
</div>
<div class="field" style="left:206px;width:256px">Full Name
  <svg width="12" height="13" viewBox="0 0 12 13"><circle cx="6" cy="3.5" r="3" fill="#666"/><path d="M0 13 C0 7 12 7 12 13 Z" fill="#666"/></svg>
</div>
<div class="field" style="left:500px;width:272px">Email Address
  <svg width="14" height="11" viewBox="0 0 14 11"><rect width="14" height="11" rx="1" fill="#666"/><path d="M1 1 L7 6 L13 1" stroke="#fff" stroke-width="1.3" fill="none"/></svg>
</div>
<div class="btn btn-sub">Subscribe Now</div>

<div class="ph tile" role="img" aria-label="Smiling boy at a dental check-up" style="left:0;background:linear-gradient(150deg,#8fb2d6,#e9d7c4 60%,#b7cf7a)"></div>
<div class="ph tile" role="img" aria-label="Dental team reviewing notes together" style="left:243px;background:linear-gradient(150deg,#e4e6e7,#b9c3cb)"></div>
<div class="ph tile" role="img" aria-label="Dentist with a patient in a teal chair" style="left:485px;background:linear-gradient(150deg,#cfe0e3,#6fb3bd 50%,#4a6fb0)"></div>
<div class="ph tile" role="img" aria-label="Dentist reviewing an x-ray on screen" style="left:728px;background:linear-gradient(150deg,#dfe3e6,#8aa7c4)"></div>
<div class="ph tile" role="img" aria-label="Smiling girl pointing at her teeth" style="left:970px;background:linear-gradient(150deg,#e9e2da,#c49a7c 55%,#4c6b92)"></div>
<div class="abs follow">Follow Us On Snapwell</div>

<footer class="footer">
  <div class="ph" role="img" aria-label="Faint background of a dental surgery" style="left:0;top:0;width:1200px;height:292px;background:radial-gradient(ellipse at 30% 60%,rgba(255,255,255,.25),rgba(255,255,255,0) 60%)"></div>
  <svg class="abs" style="left:0;top:0" width="1200" height="20" viewBox="0 0 1200 20">
    <path d="M0 0 H1200 V6 L1140 14 H60 L0 6 Z" fill="#f4f2ef"/>
    <path d="M60 14 H1140" stroke="#ffffff" stroke-width="3"/>
  </svg>
</footer>
<div class="abs logo footer-logo"><div class="name">BRAMBLEFORD</div><div class="sub">DENTAL PRACTICE</div></div>
<ul class="footer-nav"><li>Home</li><li>About Us</li><li>New Patients</li><li>Treatments</li><li>Fees</li><li>Contact Us</li></ul>
<div class="social on" style="left:505px" aria-label="Social profile one"><span></span></div>
<div class="social" style="left:555px" aria-label="Social profile two"><span></span></div>
<div class="social" style="left:605px" aria-label="Social profile three"><span></span></div>
<div class="social" style="left:655px" aria-label="Social profile four"><span></span></div>
<div class="copy">(C) Copyright | All Rights Reserved</div>
<div class="abs badge"><i></i>Ravelle</div>

</body>
</html>
```